Theatre Company needs a Poster design for a world premiere of "The Lantern" Play.

We are premiering a play that celebrates community in rural and regional Australia . We need a poster for A3 and A5 size and an image that can be used in our email correspondence/webpage.

Attached is some ideas the producing theatre committee has come up with, a river runs through the town itself.

Town

```html
<!DOCTYPE html>
<html lang="en">
<head>
<meta charset="utf-8">
<title>The Lantern — Poster</title>
<link href="https://fonts.googleapis.com/css2?family=Playfair+Display:wght@400&family=Bodoni+Moda:opsz,wght@6..96,400&display=swap" rel="stylesheet">
<style>
  :root {
    --night: #0e0f10;
    --paper: #f4f0ef;
    --rule: #e8c8c6;
    --river-deep: #262d2f;
    --river-mid: #4a5355;
    --river-light: #6d7678;
  }
  html, body {
    margin: 0;
    padding: 0;
    overflow: hidden;
    background: var(--night);
  }
  .poster {
    position: relative;
    width: 849px;
    height: 1200px;
    background: var(--night);
    overflow: hidden;
    color: var(--paper);
    font-family: "Playfair Display", "Bodoni Moda", serif;
  }
  .scene {
    position: absolute;
    left: 0;
    top: 0;
    width: 849px;
    height: 1200px;
  }
  .presenter {
    position: absolute;
    left: 86px;
    width: 678px;
    top: 104px;
    margin: 0;
    font-size: 25px;
    font-weight: 400;
    letter-spacing: 0.2px;
    text-align: center;
    white-space: nowrap;
  }
  .rule {
    position: absolute;
    left: 86px;
    width: 678px;
    height: 2px;
    background: var(--rule);
  }
  .rule--top { top: 164px; }
  .rule--bottom { top: 329px; }
  .title {
    position: absolute;
    left: 86px;
    width: 678px;
    top: 180px;
    margin: 0;
    font-size: 108px;
    line-height: 132px;
    font-weight: 400;
    letter-spacing: 1px;
    text-align: center;
    white-space: nowrap;
  }
  .credit {
    position: absolute;
    right: 85px;
    top: 362px;
    margin: 0;
    font-size: 22px;
    font-weight: 400;
    white-space: nowrap;
  }
  .tagline {
    position: absolute;
    right: 87px;
    top: 866px;
    margin: 0;
    font-family: "Bodoni Moda", "Playfair Display", serif;
    font-size: 68px;
    line-height: 83px;
    font-weight: 400;
    text-align: right;
  }
  .tagline span { display: block; white-space: nowrap; }
</style>
</head>
<body>
<main class="poster">
  <svg class="scene" viewBox="0 0 849 1200" role="img" aria-label="Black-and-white photograph of a river town skyline with an arched bridge and a small ferry on the water, fading into the dark sky">
    <defs>
      <linearGradient id="riverTone" x1="0" y1="0" x2="0" y2="1">
        <stop offset="0" stop-color="var(--river-deep)"/>
        <stop offset="0.35" stop-color="var(--river-mid)"/>
        <stop offset="0.6" stop-color="var(--river-light)"/>
        <stop offset="1" stop-color="var(--river-mid)"/>
      </linearGradient>
    </defs>
    <path d="M0 730 L0 560 L50 560 L50 545 L155 545 L155 730 L230 730 L230 628 L290 628 L290 660 L425 660 L425 595 L500 595 L500 560 L535 560 L535 503 L620 503 L620 560 L660 560 L660 548 L745 548 L745 600 L849 600 L849 1200 L0 1200 Z" fill="url(#riverTone)"/>
  </svg>

  <p class="presenter">MILLBROOK THEATRE COMPANY PRESENTS TO YOU</p>
  <div class="rule rule--top"></div>
  <h1 class="title">THE LANTERN</h1>
  <div class="rule rule--bottom"></div>
  <p class="credit">WRITTEN BY DANA WHITLOCK</p>

  <p class="tagline">
    <span>A river</span>
    <span>runs through</span>
    <span>the town itself</span>
  </p>
</main>
</body>
</html>
```